All-Natural Head Lice Removal company

I need a business card with my pre-existing logo. We are a new company located in Portland Oregon that goes into peoples homes to help with head lice removal. My products and approach are all- natural and also will be around children.On my current logo we used Teal Bl and the color Green. I am open to new ideas just want it simple and creative

Target Market(s)

my biggest market is families of school aged children

Industry/Entity Type

Business

Contact Information for Business Card

see upload for details from previous business card

Font styles to use
Serif

Colors
33a6d7
9bcb3b
f37122

Requirements
Must have
• Basic information/ logo put into a creative format that is catching to the eye
Nice to have
• creative

```html
<!DOCTYPE html>
<html lang="en">
<head>
<meta charset="utf-8">
<title>NitClear Business Card</title>
<link rel="stylesheet" href="https://fonts.googleapis.com/css2?family=Comic+Neue:wght@400;700&display=swap">
<style>
  :root {
    --page-bg: #e9e6e1;
    --card-white: #ffffff;
    --card-shade: #ecedee;
    --leaf-green: #8cc63f;
    --teal-blue: #5bb8e6;
    --ink: #1b1b1b;
    --grey-text: #555a5e;
  }
  * { box-sizing: border-box; margin: 0; padding: 0; }
  html, body {
    width: 1200px; height: 843px; overflow: hidden;
    background: var(--page-bg);
    font-family: "Comic Neue", "Comic Sans MS", sans-serif;
  }
  .canvas {
    width: 1200px; height: 843px;
    display: flex; align-items: center; justify-content: center; gap: 40px;
  }
  .card {
    position: relative;
    width: 540px; height: 309px;
    border-radius: 18px;
    overflow: hidden;
    background: linear-gradient(180deg, var(--card-white) 0%, var(--card-shade) 100%);
    box-shadow: 0 6px 18px rgba(0,0,0,0.18);
  }
  /* Back */
  .brand-symbol-area {
    position: absolute; left: 0; top: 40px;
    width: 170px; height: 240px;
    background: linear-gradient(135deg, #cde6f3 0%, #c9e3b0 100%);
  }
  .back-tagline {
    position: absolute; right: 30px; bottom: 90px;
    text-align: right; color: var(--grey-text);
    font-size: 18px; line-height: 1.4;
  }
  /* Front */
  .front-shapes { position: absolute; inset: 0; }
  .contact {
    position: absolute; left: 34px; top: 82px;
    color: var(--card-white);
  }
  .contact-name { font-size: 25px; font-weight: 700; letter-spacing: 0.5px; }
  .contact-role { font-size: 17px; margin-bottom: 14px; }
  .contact-line { display: flex; align-items: center; gap: 8px; font-size: 18px; line-height: 1.4; }
  .contact-line svg { width: 15px; height: 15px; flex: none; }
  .contact-service { font-size: 18px; margin-top: 16px; }
  .logo-lockup {
    position: absolute; right: 20px; top: 124px;
    display: flex; align-items: center; gap: 8px;
  }
  .logo-dot { width: 20px; height: 20px; border-radius: 50%; background: var(--leaf-green); }
  .logo-name { font-size: 28px; font-weight: 700; color: var(--ink); }
</style>
</head>
<body>
<main class="canvas">

  <section class="card card-back">
    <div class="brand-symbol-area" role="img" aria-label="Space for the brand symbol"></div>
    <p class="back-tagline">Try NitClear Today, Lice Free Tomorrow!<br>All Natural Lice Removal Services</p>
  </section>

  <section class="card card-front">
    <svg class="front-shapes" viewBox="0 0 540 309" preserveAspectRatio="none" aria-hidden="true">
      <path d="M0 0 H262 C320 60 330 190 372 309 H0 Z" fill="var(--leaf-green)"/>
      <path d="M262 0 H282 C336 70 346 200 392 309 H372 C330 190 320 60 262 0 Z" fill="var(--teal-blue)"/>
      <path d="M282 0 H290 C342 74 352 204 400 309 H392 C346 200 336 70 282 0 Z" fill="var(--ink)"/>
    </svg>

    <div class="contact">
      <p class="contact-name">Dana Whitfield</p>
      <p class="contact-role">Owner</p>
      <p class="contact-line">
        <svg viewBox="0 0 16 16"><path d="M3 1l3 3-2 2c1 2 3 4 5 5l2-2 3 3-2 3C7 15 1 9 0 4z" fill="currentColor"/></svg>
        1-855-555-NITS (6487)
      </p>
      <p class="contact-line">
        <svg viewBox="0 0 16 16"><rect x="1" y="3" width="14" height="10" fill="currentColor"/><path d="M1 3l7 6 7-6" stroke="var(--leaf-green)" stroke-width="1.5" fill="none"/></svg>
        dana@nitclear.com
      </p>
      <p class="contact-line">
        <svg viewBox="0 0 16 16"><circle cx="8" cy="8" r="7" fill="currentColor"/><path d="M1 8h14M8 1c-3 3-3 11 0 14M8 1c3 3 3 11 0 14" stroke="var(--leaf-green)" stroke-width="1.2" fill="none"/></svg>
        www.nitclear.com
      </p>
      <p class="contact-service">All Natural In-Home Lice Services</p>
    </div>

    <div class="logo-lockup">
      <span class="logo-dot"></span>
      <span class="logo-name">NitClear</span>
    </div>
  </section>

</main>
</body>
</html>
```